Automotive component supplier needs a business card design

We need a business card design for our company called Velran Global Components Ltd based in the UK. We are a supplier of interior and exterior components to premium car manufacturers such as Corvel Ashby, Hadley Fenn, Marquist and Tavarelli. We would like to see a modern business card design that uses the colour blue.

Target Market(s)

Premium automotive car manufacturers.

Industry/Entity Type

Automotive

Contact Information for Business Card

Company Name : Velran Global Components Limited
Address: 17 Marlow Yard, Upper Heath, Warwick, CV31 8QL, United Kingdom
Web Address : www.velrancomponents-example.co.uk

Font styles to use
Other font styles liked:
• Helvetica

Colors
3176b5
0255a3
85acd3
cfdeed
cee9f5
85cae6
34a6d7
0692cd
9bcb3c

Requirements
Must have
• Clear company logo and a mixture of blue colours.
Nice to have
• A high quality modern image.
Should not have
• Multiple colours.

```html
<!DOCTYPE html>
<html lang="en">
<head>
<meta charset="utf-8">
<title>Velran Global Components – Business Card</title>
<link rel="stylesheet" href="https://fonts.googleapis.com/css2?family=Arimo:wght@400;700&display=swap">
<style>
  :root {
    --card-blue: #0a8fcf;
    --lime: #9bcb3c;
    --white: #ffffff;
    --backdrop: #1c1e21;
  }
  * { box-sizing: border-box; margin: 0; padding: 0; }
  html, body {
    width: 1200px; height: 900px; overflow: hidden;
    background: var(--backdrop);
    font-family: "Arimo", Helvetica, Arial, sans-serif;
  }
  .canvas {
    width: 1200px; height: 900px;
    display: flex; flex-direction: column; align-items: center;
    justify-content: center; gap: 36px;
  }
  .card {
    position: relative; width: 720px; height: 400px;
    background: var(--card-blue); overflow: hidden; color: var(--white);
  }

  /* Front */
  .brand-mark {
    position: absolute; left: 0; right: 0; top: 120px;
    display: flex; justify-content: center; align-items: center;
  }
  .brand-mark__name {
    font-weight: 700; font-size: 78px; letter-spacing: 4px; color: var(--white);
  }
  .front-rule {
    position: absolute; left: 0; right: 0; top: 300px;
    display: flex; align-items: center; gap: 14px;
  }
  .front-rule__line { flex: 1; height: 7px; background: var(--lime); }
  .front-rule__url { font-size: 15px; color: var(--white); white-space: nowrap; }
  .front-rule__url em { font-style: normal; color: var(--lime); }

  /* Back */
  .identity { position: absolute; left: 56px; top: 118px; }
  .identity__company {
    font-weight: 700; font-size: 62px; letter-spacing: 3px; line-height: 1;
  }
  .identity__tagline { font-size: 13px; letter-spacing: 2.6px; margin-top: 6px; }
  .identity__person-block { display: inline-block; margin-top: 16px; }
  .identity__person { font-weight: 700; font-size: 24px; letter-spacing: 2px; }
  .identity__role { font-size: 16px; color: var(--lime); margin-top: 4px; text-align: right; }

  .divider {
    position: absolute; left: 406px; top: 78px; width: 2px; height: 160px; background: var(--lime);
  }
  .contact { position: absolute; left: 426px; top: 80px; font-size: 14px; line-height: 1.3; white-space: nowrap; }
  .contact__address { margin-bottom: 8px; }
  .contact__row { display: flex; align-items: center; gap: 10px; margin-top: 3px; }
  .contact__row svg { width: 12px; height: 12px; flex: none; }

  .back-rule {
    position: absolute; left: 0; right: 0; top: 300px; height: 5px; background: var(--white);
  }
  .back-rule__square {
    position: absolute; left: 440px; top: -8px; width: 22px; height: 20px;
    border-radius: 4px; background: var(--lime);
  }
  .back-base {
    position: absolute; left: 0; right: 0; bottom: 26px; height: 7px; background: var(--white);
  }
</style>
</head>
<body>
<main class="canvas">

  <section class="card card--front" aria-label="Card front">
    <div class="brand-mark">
      <span class="brand-mark__name">VELRAN</span>
    </div>
    <div class="front-rule">
      <span class="front-rule__line"></span>
      <span class="front-rule__url">www.<em>velrancomponents-example</em>.co.uk</span>
      <span class="front-rule__line"></span>
    </div>
  </section>

  <section class="card card--back" aria-label="Card back">
    <div class="identity">
      <div class="identity__company">VELRAN</div>
      <div class="identity__tagline">GLOBAL COMPONENTS</div>
      <div class="identity__person-block">
        <div class="identity__person">DORIAN KELL</div>
        <div class="identity__role">Director</div>
      </div>
    </div>

    <div class="divider"></div>

    <div class="contact">
      <div class="contact__address">17 Marlow Yard, Upper Heath<br>Warwick, CV31 8QL, UK</div>
      <div class="contact__row">
        <svg viewBox="0 0 12 12" aria-hidden="true"><path d="M2 1l2 0 1 3-1.5 1a7 7 0 0 0 3.5 3.5L8 7l3 1v2a1 1 0 0 1-1 1A9 9 0 0 1 1 2a1 1 0 0 1 1-1z" fill="#9bcb3c"/></svg>
        <span>700 555-0142</span>
      </div>
      <div class="contact__row">
        <svg viewBox="0 0 12 12" aria-hidden="true"><rect x="3" y="0.5" width="6" height="11" rx="1" fill="none" stroke="#9bcb3c" stroke-width="1.3"/><circle cx="6" cy="9.5" r="0.8" fill="#9bcb3c"/></svg>
        <span>700 555-0178</span>
      </div>
      <div class="contact__row">
        <svg viewBox="0 0 12 12" aria-hidden="true"><rect x="0.5" y="2" width="11" height="8" rx="1" fill="#9bcb3c"/><path d="M1 2.5l5 4 5-4" fill="none" stroke="#0a8fcf" stroke-width="1"/></svg>
        <span>hello@velran-example.co.uk</span>
      </div>
      <div class="contact__row">
        <svg viewBox="0 0 12 12" aria-hidden="true"><circle cx="6" cy="6" r="5.2" fill="none" stroke="#9bcb3c" stroke-width="1.2"/><path d="M0.8 6h10.4M6 0.8c-2.6 3-2.6 7.4 0 10.4M6 0.8c2.6 3 2.6 7.4 0 10.4" fill="none" stroke="#9bcb3c" stroke-width="1"/></svg>
        <span>www.velrancomponents-example.co.uk</span>
      </div>
    </div>

    <div class="back-rule"><span class="back-rule__square"></span></div>
    <div class="back-base"></div>
  </section>

</main>
</body>
</html>
```